Dental office stationary (letterhead, envelopes), business cards, presentation folders

Nothing too dental outside of the logo. I will need all stationary, presentation folders, business cards. Would prefer to stay in the colors of the logo

Gordon Patel, DDS
Bright Haven Dental Implant Center
555-318-2790
info@brighthavendental.example
4817 NW Maple Crest Rd Unit B
Harborview, ST 00000

Also need appointment date and time
And cancellation policy
I want it to say “kindly ask for
A 48hr cancellation policy to avoid incurring a cancellation fee”

Industry/Entity Type

Dental

Colors
0054AA
0677BA
7BADD7
CADEEF
E8F1F8

Requirements
Must have
• Name of your office, name of doctor, address, phone number
Should not have
• Too much tooth/dental. Only the tooth in logo

```html
<!DOCTYPE html>
<html lang="en">
<head>
<meta charset="UTF-8">
<title>Bright Haven Dental Implant Center – Business Card</title>
<link rel="stylesheet" href="https://fonts.googleapis.com/css2?family=Roboto:ital,wght@0,400;0,700;1,400;1,700&display=swap">
<style>
  :root {
    --canvas-bg: #2b2b2b;
    --card-white: #ffffff;
    --card-dark: #222222;
    --teal: #17b99e;
    --sky: #14a8e6;
    --deep-blue: #0a6fc2;
    --text-grey: #444444;
    --rule-grey: #6b6b6b;
    --light-text: #e8f1f8;
  }
  * { box-sizing: border-box; margin: 0; padding: 0; }
  html, body {
    width: 1200px; height: 900px; overflow: hidden;
    background: var(--canvas-bg);
    font-family: "Roboto", Arial, sans-serif;
  }
  .canvas { position: relative; width: 1200px; height: 900px; }
  .card {
    position: absolute; left: 320px; width: 560px; height: 320px;
    overflow: hidden;
    box-shadow: 0 10px 30px rgba(0,0,0,.45);
  }
  .card-front { top: 95px; background: var(--card-white); }
  .card-back { top: 485px; background: var(--card-dark); }
  .card-art { position: absolute; inset: 0; }

  /* front */
  .contact-block { position: absolute; left: 44px; top: 42px; }
  .doctor-name { font-weight: 700; font-style: italic; font-size: 21px; color: var(--sky); }
  .practice-name { font-size: 15px; color: var(--text-grey); margin-top: 4px; }
  .divider {
    position: absolute; left: 44px; top: 108px; width: 440px; height: 1.5px;
    background: var(--rule-grey);
  }
  .contact-list { position: absolute; left: 44px; top: 126px; list-style: none; }
  .contact-item {
    display: flex; align-items: center; gap: 7px;
    font-size: 13.5px; color: var(--text-grey); line-height: 21px;
  }
  .contact-item .accent { color: var(--teal); }
  .contact-icon { width: 13px; height: 13px; flex: none; }
  .brand-front {
    position: absolute; right: 40px; top: 48px;
    display: flex; align-items: center; gap: 8px;
  }
  .brand-dot { width: 12px; height: 12px; border-radius: 50%; background: var(--teal); }
  .brand-name {
    font-weight: 700; font-size: 22px; letter-spacing: 1px; color: var(--teal);
    text-transform: uppercase; line-height: 1.15;
  }
  .address {
    position: absolute; right: 40px; top: 228px; text-align: right;
    font-size: 14.5px; color: var(--text-grey); line-height: 21px;
  }

  /* back */
  .brand-back {
    position: absolute; left: 0; right: 0; top: 128px;
    display: flex; justify-content: center; align-items: center; gap: 12px;
  }
  .brand-back .brand-dot { width: 16px; height: 16px; }
  .brand-back .brand-name { font-size: 30px; letter-spacing: 2px; }
  .brand-back-sub {
    position: absolute; left: 0; right: 0; top: 176px; text-align: center;
    font-size: 13px; letter-spacing: 5px; color: var(--light-text); text-transform: uppercase;
  }
</style>
</head>
<body>
<main class="canvas">

  <section class="card card-front" aria-label="Business card front">
    <svg class="card-art" viewBox="0 0 560 320" preserveAspectRatio="none" aria-hidden="true">
      <defs>
        <linearGradient id="band-blue" x1="0" x2="1">
          <stop offset="0" stop-color="#14b4ee"/>
          <stop offset="1" stop-color="#0a6fc2"/>
        </linearGradient>
      </defs>
      <polygon points="0,288 258,288 250,320 0,320" fill="url(#band-blue)"/>
      <polygon points="270,292 560,292 560,320 262,320" fill="#17b99e"/>
    </svg>

    <div class="contact-block">
      <p class="doctor-name">Gordon Patel, DDS</p>
      <p class="practice-name">Bright Haven Dental Implant Center</p>
    </div>
    <div class="divider"></div>

    <ul class="contact-list">
      <li class="contact-item">
        <svg class="contact-icon" viewBox="0 0 14 14"><circle cx="7" cy="7" r="7" fill="#17b99e"/><path d="M4.5 3.5l1.5 0 .6 1.8-.9.7a5 5 0 0 0 2.3 2.3l.7-.9 1.8.6v1.5a1 1 0 0 1-1 1A6 6 0 0 1 3.5 4.5a1 1 0 0 1 1-1z" fill="#fff"/></svg>
        555-318-2790
      </li>
      <li class="contact-item">
        <svg class="contact-icon" viewBox="0 0 14 14"><circle cx="7" cy="7" r="7" fill="#17b99e"/><rect x="3.5" y="4.5" width="7" height="5" fill="none" stroke="#fff" stroke-width="1"/><path d="M3.5 4.5L7 7.3l3.5-2.8" fill="none" stroke="#fff" stroke-width="1"/></svg>
        info@brighthavendental.example
      </li>
      <li class="contact-item">
        <svg class="contact-icon" viewBox="0 0 14 14"><circle cx="7" cy="7" r="7" fill="#17b99e"/><circle cx="7" cy="7" r="3.5" fill="none" stroke="#fff" stroke-width="1"/><path d="M3.5 7h7M7 3.5v7" stroke="#fff" stroke-width="1"/></svg>
        <span>www.<span class="accent">brighthavendental</span>.example</span>
      </li>
    </ul>

    <div class="brand-front">
      <span class="brand-dot"></span>
      <span class="brand-name">Bright Haven</span>
    </div>

    <p class="address">4817 NW Maple Crest Rd Unit B<br>Harborview, ST 00000</p>
  </section>

  <section class="card card-back" aria-label="Business card back">
    <svg class="card-art" viewBox="0 0 560 320" preserveAspectRatio="none" aria-hidden="true">
      <defs>
        <linearGradient id="arc-blue" x1="0" x2="1">
          <stop offset="0" stop-color="#14b4ee"/>
          <stop offset="1" stop-color="#0a6fc2"/>
        </linearGradient>
      </defs>
      <path d="M120 0 C300 10 470 90 560 250 L560 0 Z" fill="#17b99e"/>
      <path d="M120 0 C300 10 470 90 560 250 L560 236 C470 84 310 14 150 0 Z" fill="url(#arc-blue)"/>
    </svg>
    <div class="brand-back">
      <span class="brand-dot"></span>
      <span class="brand-name">Bright Haven</span>
    </div>
    <p class="brand-back-sub">Dental Implant Center</p>
  </section>

</main>
</body>
</html>
```